Verodex business card

Business card for sustainable investment company called "Verodex". Verodex is an exchange platform selling carbon credits between buyers and sellers. Carbon Credits are an environmental commodity for reducing global carbon emissions.

the card should obviously have our logo and the theme should be sustainability/environment mixed with a trading platform.

Contact Information for Business Card

Logo, Name, Title, Phone, Email

Colors
0054AA
0677BA
7BADD7
CADEEF
E8F1F8
0094D4
00A9DD
6FCCEA
C7EBF8
E9F6FB
00AB8E
00BBA5
67D7C9
C6EFE9
E9F9F6
59FF00
82FF00
B8FF75
E3FFCB
F4FFEA

```html
<!DOCTYPE html>
<html lang="en">
<head>
<meta charset="utf-8">
<title>Verodex business card</title>
<link href="https://fonts.googleapis.com/css2?family=Montserrat:wght@400;500;600;700&display=swap" rel="stylesheet">
<style>
  :root {
    --navy: #14284f;
    --sky: #2fb6ec;
    --blue: #3f7fd0;
    --ink: #1b2233;
    --paper: #ffffff;
    --table: #e6e8ec;
  }
  * { margin: 0; padding: 0; box-sizing: border-box; }
  html, body { width: 1200px; height: 900px; overflow: hidden; }
  body {
    background: var(--table);
    font-family: "Montserrat", sans-serif;
    display: flex; flex-direction: column; align-items: center; justify-content: center;
    gap: 40px;
  }
  .card {
    width: 630px; height: 360px; position: relative; overflow: hidden;
    box-shadow: 0 10px 30px rgba(0,0,0,.18);
  }
  .card-front { background: var(--navy); display: flex; align-items: center; justify-content: center; }
  .brand { display: flex; align-items: center; gap: 22px; }
  .brand-dot { width: 46px; height: 46px; border-radius: 50%; background: var(--sky); }
  .brand-name { font-weight: 600; font-size: 58px; letter-spacing: 1px; color: var(--paper); line-height: 1; }
  .card-back { background: var(--paper); }
  .card-back .brand { position: absolute; left: 70px; top: 60px; gap: 20px; }
  .card-back .brand-dot { width: 40px; height: 40px; }
  .card-back .brand-name { color: var(--navy); font-size: 50px; }
  .details { position: absolute; left: 70px; top: 148px; display: flex; gap: 18px; align-items: stretch; }
  .person { text-align: right; padding-top: 4px; }
  .person-name { font-weight: 700; font-size: 24px; letter-spacing: .5px; line-height: 1.1; }
  .person-first { color: var(--sky); }
  .person-last { color: var(--navy); }
  .person-title { font-weight: 500; font-size: 15px; color: var(--ink); margin-top: 6px; }
  .divider { width: 1.5px; background: var(--sky); }
  .contacts { list-style: none; display: flex; flex-direction: column; gap: 6px; font-size: 14px; color: var(--ink); }
  .contacts li { display: flex; align-items: center; gap: 8px; }
  .contacts svg { width: 14px; height: 14px; flex: none; }
  .wave { position: absolute; left: 0; bottom: 0; width: 630px; height: 170px; }
</style>
</head>
<body>
  <section class="card card-front">
    <div class="brand">
      <span class="brand-dot"></span>
      <span class="brand-name">VERODEX</span>
    </div>
  </section>

  <section class="card card-back">
    <div class="brand">
      <span class="brand-dot"></span>
      <span class="brand-name">VERODEX</span>
    </div>
    <div class="details">
      <div class="person">
        <p class="person-name"><span class="person-first">DANIEL</span> <span class="person-last">HARKER</span></p>
        <p class="person-title">Co-Founder</p>
      </div>
      <span class="divider"></span>
      <ul class="contacts">
        <li><svg viewBox="0 0 16 16"><path fill="#2fb6ec" d="M3 1l3 3-2 2c1 2 3 4 5 5l2-2 3 3-2 3C6 14 2 10 0 3z"/></svg>555-210-4836</li>
        <li><svg viewBox="0 0 16 16"><rect x="1" y="3" width="14" height="10" fill="#3f7fd0"/><path d="M1 3l7 6 7-6" stroke="#fff" stroke-width="1.4" fill="none"/></svg>info@verodex.com</li>
        <li><svg viewBox="0 0 16 16"><circle cx="8" cy="8" r="7" fill="#3f7fd0"/><path d="M1 8h14M8 1c-3 4-3 10 0 14M8 1c3 4 3 10 0 14" stroke="#fff" stroke-width="1" fill="none"/></svg>www.verodex.com</li>
      </ul>
    </div>
    <svg class="wave" viewBox="0 0 630 170" preserveAspectRatio="none" aria-hidden="true">
      <defs>
        <linearGradient id="stripe" x1="0" x2="1">
          <stop offset="0" stop-color="#2fb6ec"/>
          <stop offset="1" stop-color="#3f7fd0"/>
        </linearGradient>
      </defs>
      <path d="M0 150 C 220 150, 380 40, 630 10 L630 170 L0 170 Z" fill="url(#stripe)"/>
      <path d="M0 160 C 230 158, 390 52, 630 20 L630 170 L0 170 Z" fill="#14284f"/>
    </svg>
  </section>
</body>
</html>
```